Vehicle Rental Hire in the Algarve - Portugal

We are opening a Vehicle Rental company in the Algarve - Portugal - this will attract both locals and Tourists visiting. So we want this website to capture the beautiful location we will be set in, along with the familiarity of a vehicle rental company. And to keep a colour scheme in Line with out Logo. We are Quenmira Vehicle Rental.

Industry/Entity Type

Vehicle Rental

Number of Pages Required

1 page

Requirements
Must have
• must be professional, and simple to use navigation bar - must also have a "make a reservation" box - similar to the screenshot attached - Under our logo it must read "Vehicle Rental"
Nice to have
• It needs to be in a colour scheme that fits in with our logo

```html
<!DOCTYPE html>
<html lang="en">
<head>
<meta charset="utf-8">
<title>Quenmira Vehicle Rental</title>
<link rel="stylesheet" href="https://fonts.googleapis.com/css2?family=Open+Sans:wght@400;600&family=Ubuntu:wght@500;700&display=swap">
<style>
:root{
  --blue:#1a10d8;
  --red:#c4262b;
  --purple:#5a1fa8;
  --text:#555;
  --white:#fff;
  --dark:#222;
}
*{box-sizing:border-box;margin:0;padding:0}
html,body{width:1200px;height:2770px;overflow:hidden;background:var(--white)}
body{position:relative;font-family:"Open Sans",sans-serif;color:var(--text)}
.abs{position:absolute}
.center{left:0;width:1200px;text-align:center}
.head{font-family:"Ubuntu",sans-serif;font-weight:700}

/* hero */
.hero{top:0;left:0;width:1200px;height:597px;background:linear-gradient(180deg,#3a3f4a 0%,#4a4540 40%,#2c2a2e 100%)}
.hero-shade{top:0;left:0;width:1200px;height:597px;background:radial-gradient(ellipse at 60% 70%,rgba(190,140,80,.35),transparent 60%)}
.logo{left:130px;top:36px;width:122px;height:122px;border:3px solid var(--white);border-radius:50%;display:flex;flex-direction:column;align-items:center;justify-content:center;gap:2px;color:var(--white)}
.logo-name{font-family:"Ubuntu",sans-serif;font-weight:500;font-size:19px;line-height:1}
.logo-tag{font-family:"Open Sans",sans-serif;font-size:10.5px;line-height:1.2}
.nav{left:302px;top:62px;width:898px;height:69px;border-radius:35px 0 0 35px;background:linear-gradient(90deg,var(--purple),#c12c3a 40%,#8a2068 75%,var(--purple));display:flex;align-items:center;padding-left:60px;gap:35px}
.nav a{font-family:"Open Sans",sans-serif;font-weight:600;font-size:14.5px;color:var(--white);text-decoration:none}
.hero-title{top:280px;font-size:60px;color:var(--white);letter-spacing:.5px}
.hero-sub{top:376px;font-size:25px;color:var(--white)}
.btn{display:flex;align-items:center;justify-content:center;gap:12px;border-radius:23px;font-family:"Ubuntu",sans-serif;font-weight:700;font-size:17px}
.btn svg{width:15px;height:15px}
.btn-light{left:443px;top:441px;width:148px;height:44px;background:var(--white);color:var(--red)}
.btn-red{left:607px;top:441px;width:150px;height:44px;background:var(--red);color:var(--white)}

/* about */
.about-title{left:113px;top:764px;font-size:52px;color:var(--blue)}
.rule{height:2px;background:var(--red)}
.about-text{left:113px;top:874px;width:440px;font-size:15.5px;line-height:30.7px}
.about-text p+p{margin-top:30.7px}
.btn-blue{left:113px;top:1236px;width:149px;height:44px;background:var(--blue);color:var(--white)}

/* reservation */
.booking{left:600px;top:714px;width:487px;height:627px;border-radius:70px;background:linear-gradient(170deg,#c4262b 0%,#a02650 30%,#6a20a0 65%,var(--purple) 100%);overflow:hidden}
.booking-title{left:0;top:73px;width:487px;text-align:center;font-size:32px;color:var(--white)}
.booking .rule-b{left:143px;top:127px;width:202px;height:2px;background:var(--blue)}
.field{height:50px;border-radius:25px;background:var(--white);display:flex;align-items:center;justify-content:space-between;padding:0 22px;font-size:14px;color:#666}
.field svg{width:10px;height:10px}
.check{left:40px;top:234px;display:flex;align-items:center;gap:12px;font-size:13px;color:var(--white)}
.check i{width:12px;height:12px;background:var(--white);display:block}
.search{left:40px;top:495px;width:406px;height:50px;border-radius:25px;background:var(--red);color:var(--white);display:flex;align-items:center;justify-content:center;font-family:"Ubuntu",sans-serif;font-weight:700;font-size:20px}

/* offer */
.offer-title{top:1458px;font-size:52px;color:var(--blue)}
.offer{width:300px;height:300px;border-radius:50%;overflow:hidden;top:1592px;background:linear-gradient(160deg,#8a8a90,#3c3c42);box-shadow:0 10px 25px rgba(0,0,0,.15)}
.offer-band{left:0;top:200px;width:300px;height:100px;background:var(--red);border-radius:150px 150px 0 0/60px 60px 0 0;display:flex;flex-direction:column;align-items:center;padding-top:14px;gap:10px;font-family:"Ubuntu",sans-serif;font-weight:700;font-size:15.5px;color:var(--white)}
.offer-band svg{width:34px;height:34px}
.arrow{top:1732px;width:20px;height:20px;border-radius:50%}

/* support */
.support{left:0;top:2018px;width:1200px;height:353px;background:linear-gradient(180deg,#2218e0,#1a10d4 60%,#2a1fd8)}
.support-title{top:2090px;font-size:52px;color:var(--white)}
.support-sub{top:2192px;font-size:23px;color:var(--white)}
.support-phone{top:2236px;font-size:54px;color:var(--white)}

/* footer */
.foot-logo{left:540px;top:2430px;width:120px;height:120px;border:2px solid var(--blue);border-radius:50%;display:flex;flex-direction:column;align-items:center;justify-content:center;gap:2px;color:var(--blue)}
.foot-nav{top:2580px;display:flex;justify-content:center;gap:35px}
.foot-nav a{font-size:14.5px;color:#555;text-decoration:none}
.social{top:2634px;width:40px;height:40px;border-radius:50%;background:var(--red);display:flex;align-items:center;justify-content:center}
.social svg{width:16px;height:16px}
.copy{top:2700px;font-size:13.5px;color:#666}
.bottom-line{left:0;top:2765px;width:1200px;height:5px;background:var(--red)}
</style>
</head>
<body>

<section>
  <div class="abs hero" role="img" aria-label="Evening aerial view of a busy city highway with traffic"></div>
  <div class="abs hero-shade"></div>
  <div class="abs logo"><span class="logo-name">QUENMIRA</span><span class="logo-tag">Vehicle Rental</span></div>
  <nav class="abs nav">
    <a href="#">HOME</a><a href="#">FLEET</a><a href="#">PROMOTIONS</a><a href="#">EXTRAS &amp; SERVICES</a><a href="#">ABOUT US</a><a href="#">PARTNERS</a><a href="#">CONTACT US</a>
  </nav>
  <h1 class="abs center head hero-title">QUENMIRA VEHICLE RENTAL</h1>
  <p class="abs center hero-sub">Vehicle Rental company in the Algarve - Portugal</p>
  <a class="abs btn btn-light">Contact Us <svg viewBox="0 0 16 16"><circle cx="8" cy="8" r="8" fill="currentColor"/><path d="M4 8h7M8 5l3 3-3 3" stroke="#fff" stroke-width="2" fill="none"/></svg></a>
  <a class="abs btn btn-red">Get Started <svg viewBox="0 0 16 16"><circle cx="8" cy="8" r="8" fill="#fff"/><path d="M4 8h7M8 5l3 3-3 3" stroke="#c4262b" stroke-width="2" fill="none"/></svg></a>
</section>

<section>
  <h2 class="abs head about-title">ABOUT US</h2>
  <div class="abs rule" style="left:113px;top:839px;width:202px"></div>
  <div class="abs about-text">
    <p>I must explain to you how all this mistaken idea of denouncing pleasure and praising pain was born and I will give you a complete account of the system, and expound the actual teachings of the great explorer of the truth, the master-builder of human happiness.</p>
    <p>No one rejects, dislikes, or avoids pleasure itself, because it is pleasure, but because those who do not know how to pursue pleasure rationally encounter consequences that are extremely painful. Nor again is there anyone who loves or pursues or desires to obtain</p>
  </div>
  <a class="abs btn btn-blue">Read More <svg viewBox="0 0 16 16"><circle cx="8" cy="8" r="8" fill="#fff"/><path d="M4 8h7M8 5l3 3-3 3" stroke="#1a10d8" stroke-width="2" fill="none"/></svg></a>

  <form class="abs booking">
    <h3 class="abs head booking-title">MAKE A RESERVATION</h3>
    <div class="abs rule-b"></div>
    <div class="abs field" style="left:40px;top:164px;width:406px">Pickup Location <svg viewBox="0 0 10 10"><path d="M2 4l3 3 3-3" stroke="#666" fill="none"/></svg></div>
    <div class="abs check"><i></i>Pick up location same as return location</div>
    <div class="abs field" style="left:40px;top:272px;width:194px">Driver's age <svg viewBox="0 0 10 10"><path d="M2 4l3 3 3-3" stroke="#666" fill="none"/></svg></div>
    <div class="abs field" style="left:252px;top:272px;width:194px">Vehicle category <svg viewBox="0 0 10 10"><path d="M2 4l3 3 3-3" stroke="#666" fill="none"/></svg></div>
    <div class="abs field" style="left:40px;top:344px;width:194px">Pick up date <svg viewBox="0 0 10 10"><path d="M2 4l3 3 3-3" stroke="#666" fill="none"/></svg></div>
    <div class="abs field" style="left:252px;top:344px;width:194px">Hour <svg viewBox="0 0 10 10"><path d="M2 4l3 3 3-3" stroke="#666" fill="none"/></svg></div>
    <div class="abs field" style="left:40px;top:415px;width:194px">Drop off date <svg viewBox="0 0 10 10"><path d="M2 4l3 3 3-3" stroke="#666" fill="none"/></svg></div>
    <div class="abs field" style="left:252px;top:415px;width:194px">Hour <svg viewBox="0 0 10 10"><path d="M2 4l3 3 3-3" stroke="#666" fill="none"/></svg></div>
    <div class="abs search">Search Here</div>
  </form>
</section>

<section>
  <h2 class="abs center head offer-title">WHAT WE OFFER</h2>
  <div class="abs rule" style="left:499px;top:1534px;width:202px"></div>
  <svg class="abs arrow" style="left:68px" viewBox="0 0 20 20"><circle cx="10" cy="10" r="10" fill="#ccc"/><path d="M15 10H6M9 6l-4 4 4 4" stroke="#fff" stroke-width="2" fill="none"/></svg>
  <svg class="abs arrow" style="left:1109px" viewBox="0 0 20 20"><circle cx="10" cy="10" r="10" fill="#222"/><path d="M5 10h9M11 6l4 4-4 4" stroke="#fff" stroke-width="2" fill="none"/></svg>

  <div class="abs offer" style="left:116px" role="img" aria-label="Hands holding a phone with a ride app inside a car">
    <div class="abs offer-band"><svg viewBox="0 0 34 34" fill="none" stroke="#fff" stroke-width="2"><rect x="4" y="14" width="20" height="10" rx="2"/><path d="M7 14l3-6h8l3 6"/><circle cx="9" cy="26" r="2"/><circle cx="19" cy="26" r="2"/><path d="M26 6l4 4-6 12"/></svg>TRAVEL ASSISTANCE</div>
  </div>
  <div class="abs offer" style="left:450px" role="img" aria-label="Child secured in a rear-facing car seat">
    <div class="abs offer-band"><svg viewBox="0 0 34 34" fill="none" stroke="#fff" stroke-width="2"><rect x="9" y="4" width="16" height="26" rx="5"/><path d="M13 4l4 12 4-12M12 30l5-10 5 10"/></svg>BABY SEAT</div>
  </div>
  <div class="abs offer" style="left:783px" role="img" aria-label="Smiling man driving a car">
    <div class="abs offer-band"><svg viewBox="0 0 34 34" fill="none" stroke="#fff" stroke-width="2"><circle cx="17" cy="17" r="14"/><circle cx="17" cy="17" r="4"/><path d="M4 15c8-3 18-3 26 0M14 20l-4 10M20 20l4 10"/></svg>ADDITIONAL DRIVER</div>
  </div>
</section>

<section>
  <div class="abs support" role="img" aria-label="Blue-tinted view of highway traffic"></div>
  <h2 class="abs center head support-title">CALL FOR A CUSTOMER SUPPORT</h2>
  <div class="abs rule" style="left:499px;top:2165px;width:202px"></div>
  <p class="abs center support-sub">Vehicle Rental company in Algarve - Portugal</p>
  <p class="abs center head support-phone">+1 555 014 2290</p>
</section>

<footer>
  <div class="abs foot-logo"><span class="logo-name">QUENMIRA</span><span class="logo-tag">Vehicle Rental</span></div>
  <nav class="abs center foot-nav">
    <a href="#">HOME</a><a href="#">FLEET</a><a href="#">PROMOTIONS</a><a href="#">EXTRAS &amp; SERVICES</a><a href="#">ABOUT US</a><a href="#">PARTNERS</a><a href="#">CONTACT US</a>
  </nav>
  <div class="abs rule" style="left:113px;top:2653px;width:404px;height:1px"></div>
  <div class="abs rule" style="left:683px;top:2653px;width:404px;height:1px"></div>
  <a class="abs social" style="left:533px" aria-label="Share"><svg viewBox="0 0 16 16" fill="none" stroke="#fff" stroke-width="1.6"><circle cx="4" cy="8" r="2"/><circle cx="12" cy="3.5" r="2"/><circle cx="12" cy="12.5" r="2"/><path d="M6 7l4-2.5M6 9l4 2.5"/></svg></a>
  <a class="abs social" style="left:580px" aria-label="Email"><svg viewBox="0 0 16 16" fill="none" stroke="#fff" stroke-width="1.6"><rect x="2" y="3.5" width="12" height="9" rx="1"/><path d="M2 4l6 5 6-5"/></svg></a>
  <a class="abs social" style="left:627px" aria-label="Phone"><svg viewBox="0 0 16 16" fill="none" stroke="#fff" stroke-width="1.6"><path d="M4 2l2.5 3-1.5 1.5c.8 1.8 2.2 3.2 4 4L10.5 9l3 2.5-1.5 2C7 13 3 9 2.5 4z"/></svg></a>
  <p class="abs center copy">(C) Copyright 2024 | All Rights Reserved</p>
  <div class="abs bottom-line"></div>
</footer>

</body>
</html>
```